Mortgage Company ready to make a statement!

We have a basic logo that I am fairly happy with ... but it could use a little bit of tweaking before we order the sign for our building. We also want some knock-your-socks-off business cards.
Problem: Inside of our Mortgage Office (Bright Fern Mortgage Group), we are going to have a coffee lounge (Sunbrew Cafe) for Realtors to use instead of the local Cuppington to meet with homebuyers. The office and coffee lounge are in an industrial building and is decorated with cozy overstuffed chairs, a hodge podge of interesting lamps and furniture, and goal is to make it as inviting as possible. However, we are a financial institution... so we need to keep it pretty clean as well.
One of my favorite marketing ideas is to cut a house key for everyone who buys a home using us with a key that matches our logo. There's only one key shape that works really well, so that needs to match the logo in order for the idea to work. I'll attach an image of the key blank.... although the way the key hole cut out looks terrible, so I was thinking of having them just do a thin outline instead.
Would like a similar, matching logo for the Sunbrew Cafe... but possibly something that would be a little less formal and would be cute on a coffee mug- nothing stuffy.
AND, we're opening a home inspection company as well, and we would like that logo and branding to match. The home inspection company is "Bright Fern Home Inspections"
We were thinking that for the home inspection company , we could use a magnifying glass shape inside of the house shape for the logo, use a keyhole shape inside of the same house for the mortgage company, and use a coffee cup inside of the house shape for Sunbrew Cafe.
Just getting stuck and need to help. I designed the attached logo myself, and that is what we are currently using. Designers at local printing companies have failed to impress us.
The mortgage industry has a lot of numbers and logos, etc that they require us to put on our business cards... so it's hard to keep them looking clean.
HELP! HELP! :)

```html
<!DOCTYPE html>
<html lang="en">
<head>
<meta charset="utf-8">
<title>Bright Fern Mortgage Group – Business Card</title>
<link rel="stylesheet" href="https://fonts.googleapis.com/css2?family=Open+Sans:wght@300;400;600;700&display=swap">
<style>
  :root {
    --backdrop: #dcd8d3;
    --card-top: #f4f2f1;
    --divider: #51565c;
    --band: #22678a;
    --brand: #225f7f;
    --on-band: #ffffff;
  }
  * { margin: 0; padding: 0; box-sizing: border-box; }
  html, body {
    width: 1200px; height: 900px; overflow: hidden;
    background: var(--backdrop);
    font-family: "Open Sans", Arial, sans-serif;
  }
  .business-card {
    position: absolute; left: 100px; top: 140px;
    width: 1000px; height: 620px;
    background: var(--card-top);
    box-shadow: 0 18px 40px rgba(0,0,0,0.18);
    overflow: hidden;
  }
  .brand-area {
    position: absolute; left: 0; top: 0; width: 100%; height: 362px;
    display: flex; align-items: center; justify-content: center; gap: 28px;
  }
  .brand-dot {
    width: 70px; height: 70px; border-radius: 50%;
    background: var(--brand);
  }
  .brand-name {
    color: var(--brand); font-weight: 300;
    font-size: 62px; line-height: 1.1; letter-spacing: 1px;
  }
  .divider-line {
    position: absolute; left: 0; top: 362px; width: 100%; height: 7px;
    background: var(--divider);
  }
  .contact-band {
    position: absolute; left: 0; top: 369px; width: 100%; height: 251px;
    background: var(--band); color: var(--on-band);
  }
  .person {
    position: absolute; right: 530px; top: 60px; text-align: right;
  }
  .person-name { font-weight: 700; font-size: 31px; letter-spacing: 0.5px; }
  .person-title { font-weight: 400; font-size: 25px; margin-top: 4px; }
  .band-rule {
    position: absolute; left: 498px; top: 58px; width: 2px; height: 96px;
    background: var(--on-band);
  }
  .contact-list {
    position: absolute; left: 522px; top: 44px; list-style: none;
    font-size: 26px; line-height: 37px;
  }
  .contact-list li { display: flex; align-items: center; gap: 12px; }
  .contact-list svg { width: 18px; height: 18px; fill: var(--on-band); flex: none; }
  .address {
    position: absolute; left: 0; top: 182px; width: 100%;
    text-align: center; font-size: 26px; padding-left: 60px;
  }
</style>
</head>
<body>
  <div class="business-card">
    <div class="brand-area">
      <div class="brand-dot"></div>
      <div class="brand-name">Bright Fern<br>Mortgage Group</div>
    </div>
    <div class="divider-line"></div>
    <div class="contact-band">
      <div class="person">
        <div class="person-name">DANIEL MARSH</div>
        <div class="person-title">Managing Director</div>
      </div>
      <div class="band-rule"></div>
      <ul class="contact-list">
        <li>
          <svg viewBox="0 0 24 24" aria-hidden="true"><path d="M6.6 10.8a15.1 15.1 0 0 0 6.6 6.6l2.2-2.2c.3-.3.7-.4 1-.2 1.1.4 2.3.6 3.6.6.6 0 1 .4 1 1V20c0 .6-.4 1-1 1A17 17 0 0 1 3 4c0-.6.4-1 1-1h3.5c.6 0 1 .4 1 1 0 1.3.2 2.5.6 3.6.1.3 0 .7-.2 1z"/></svg>
          (044)555018273
        </li>
        <li>
          <svg viewBox="0 0 24 24" aria-hidden="true"><path d="M2 5h20v14H2z M2 5l10 8 10-8" fill="none" stroke="#fff" stroke-width="0"/><path d="M2 5h20v2l-10 7L2 7z M2 9l10 7 10-7v10H2z"/></svg>
          info@brightfernmortgage.com
        </li>
        <li>
          <svg viewBox="0 0 24 24" aria-hidden="true"><circle cx="12" cy="12" r="10"/></svg>
          www.brightfernmortgage.com
        </li>
      </ul>
      <div class="address">1234, Address GoesHere, Country name, 12345</div>
    </div>
  </div>
</body>
</html>
```